Professional Single Page Website Design for Tollbrook Advisory

Tollbrook Advisory is a new business consultancy specializing in providing expert services to small businesses, primarily in the brick-and-mortar retail and food service sectors. We offer a range of services including franchise development and launch, due diligence, and construction management.

Currently, we have a basic website set up at www.tollbrookadvisory.example, but we need a professional touch to enhance its design and functionality.

Project Requirements:
- Single Page Design: For now, we need a single page design that effectively showcases who we are, our services, and contact information.
- Future Expansion: The design should be flexible and scalable for future expansion to include additional pages like specific service offerings, about us, and a dedicated contact page.
- Design Aesthetic: We are looking for a modern yet professional design that aligns with our brand identity.
- Logo: We have a logo that we like, which was also sourced from Pixel Bazaar. The logo files are attached to this project brief.

Key Sections to Include:
- Hero Section: An engaging introduction to Tollbrook Advisory with a strong visual impact.
- About Us: A brief overview of who we are and our mission.
- Team: Section for the profiles of the two principals.
- Services: A clear and concise presentation of our services, including franchise development, due diligence, and construction management.
- Contact Information: Easy-to-find contact details, including a form for inquiries.
- Call to Action: Encouraging visitors to get in touch with us for consultations or further information.

Design Considerations:
- Ensure the design is responsive and mobile-friendly.
- Include high-quality images and icons that complement our services and industry.
- We do not need development services, this is only a design project.

```html
<!DOCTYPE html>
<html lang="en">
<head>
<meta charset="utf-8">
<title>Tollbrook Advisory</title>
<link href="https://fonts.googleapis.com/css2?family=Poppins:wght@300;400;500;600;700&display=swap" rel="stylesheet">
<style>
:root{
  --ink:#1f2a33;
  --dark:#25323b;
  --green:#8fc6a7;
  --green-deep:#6fb38e;
  --mint:#e8f1ed;
  --mint-2:#dbe9e2;
  --line:#e3e9e6;
  --text:#333c42;
  --white:#ffffff;
}
*{box-sizing:border-box;margin:0;padding:0}
html,body{width:1200px;height:4323px;overflow:hidden}
body{position:relative;background:var(--white);font-family:"Poppins",sans-serif;color:var(--text)}
.abs{position:absolute}

/* decorative background shapes */
.blob{position:absolute;background:var(--mint);border-radius:120px;transform:rotate(45deg)}

/* header */
.site-header{position:absolute;left:0;top:0;width:1200px;height:154px;background:var(--white);z-index:5}
.brand{position:absolute;left:75px;top:50px;display:flex;align-items:center;gap:14px}
.brand-dot{width:54px;height:54px;border-radius:50%;background:var(--green)}
.brand-name{font-weight:600;font-size:30px;color:var(--ink);letter-spacing:-.5px}
.main-nav{position:absolute;top:74px;left:609px;display:flex;gap:0}
.main-nav a{position:absolute;font-size:14.5px;color:var(--ink);text-decoration:none;white-space:nowrap;letter-spacing:.3px}
.main-nav a.active::after{content:"";position:absolute;left:0;right:0;bottom:-8px;height:2px;background:var(--green)}

/* hero */
.hero{position:absolute;left:0;top:154px;width:1200px;height:695px;overflow:hidden;
  background:linear-gradient(180deg,#5fa9d3 0%,#9ccbe4 45%,#cfdfe6 75%,#8e9aa2 100%)}
.hero-towers{position:absolute;left:0;bottom:0;width:760px;height:360px;background:linear-gradient(180deg,#8fb2c4,#5d7482)}
.hero-building{position:absolute;right:0;top:0;width:327px;height:695px;background:linear-gradient(90deg,#c7a79c,#d9bdb1 60%,#bf9d92)}
.hero-mid{position:absolute;left:750px;top:395px;width:130px;height:300px;background:linear-gradient(180deg,#f1f1ee,#c9cdcc)}
.hero-shape{position:absolute;left:90px;top:36px;width:560px;height:560px;border-radius:150px;transform:rotate(45deg);background:rgba(232,242,244,.78)}
.hero-copy{position:absolute;left:0;top:0;width:712px;text-align:center;color:var(--ink)}
.hero-title{position:absolute;left:0;width:712px;top:212px;font-size:59px;font-weight:700;letter-spacing:-.5px}
.hero-sub{position:absolute;left:0;width:712px;top:280px;font-size:45px;font-weight:400}
.hero-kicker{position:absolute;left:0;width:712px;top:356px;font-size:27px;font-weight:400}
.hero-kicker2{position:absolute;left:0;width:712px;top:390px;font-size:27px;font-weight:600}

/* pill button */
.pill{position:absolute;display:flex;align-items:center;border-radius:40px;background:var(--dark);color:var(--white);font-weight:600;font-size:16px;letter-spacing:.3px;padding-left:20px}
.pill .knob{position:absolute;right:6px;top:50%;transform:translateY(-50%);width:46px;height:46px;border-radius:50%;background:var(--green)}
.pill.light{background:var(--green)}
.pill.light .knob{background:#b7ddc8}

/* section headings */
.h2{position:absolute;font-size:57px;font-weight:600;color:var(--ink);letter-spacing:-.5px;line-height:1}
.kicker{position:absolute;font-size:24px;color:var(--green);display:flex;align-items:center;gap:14px;white-space:nowrap}
.kicker .rule{display:inline-block;width:76px;height:2px;background:var(--ink)}
.kicker .rule.short{width:34px}

/* about */
.about-text{position:absolute;left:100px;top:1150px;width:456px;font-size:13.5px;line-height:22.6px;color:var(--ink)}
.about-photo{position:absolute;left:640px;top:980px;width:480px;height:480px;border-radius:110px;transform:rotate(45deg);overflow:hidden;
  background:linear-gradient(135deg,#c9d6de,#a89c90 50%,#6f6a63)}
.about-halo{position:absolute;left:620px;top:960px;width:520px;height:520px;border-radius:120px;transform:rotate(45deg);background:#eef2f1}

/* service cards */
.svc-card{position:absolute;background:var(--white);border-radius:14px;box-shadow:0 0 12px rgba(143,198,167,.45);text-align:center;overflow:visible}
.svc-card.featured{border:2px solid var(--dark);box-shadow:none}
.svc-img{position:absolute;left:8px;right:8px;top:8px;height:196px;border-radius:4px}
.svc-icon{position:absolute;left:50%;margin-left:-38px;width:76px;height:76px;border-radius:50%;background:#e7f3ec;display:flex;align-items:center;justify-content:center;border:4px solid var(--white)}
.svc-title{position:absolute;left:0;right:0;font-size:20px;font-weight:500;color:var(--ink)}
.svc-desc{position:absolute;left:30px;right:30px;font-size:13.5px;line-height:21.5px;color:var(--ink)}

/* team */
.team-card{position:absolute;width:322px;height:448px;background:var(--white);border-radius:12px;box-shadow:0 0 10px rgba(0,0,0,.08)}
.team-photo{position:absolute;left:8px;top:8px;width:306px;height:234px;border-radius:4px}
.team-name{position:absolute;left:26px;top:266px;font-size:23px;font-weight:500;color:var(--ink)}
.team-role{position:absolute;left:26px;top:297px;font-size:19px;color:var(--green)}
.team-rule{position:absolute;left:26px;top:336px;width:200px;height:1px;background:#c9cfcc}
.team-ico{position:absolute;top:318px;width:34px;height:34px;border-radius:8px;background:var(--dark);transform:rotate(45deg);display:flex;align-items:center;justify-content:center}
.team-ico svg{transform:rotate(-45deg)}
.team-bio{position:absolute;left:26px;top:362px;width:270px;font-size:13.5px;line-height:22px;color:var(--ink)}

/* contact */
.contact-lead{position:absolute;left:126px;top:3330px;width:480px;font-size:22px;line-height:31px;color:var(--ink)}
.field{position:absolute;background:var(--white);border:1px solid var(--line);box-shadow:0 2px 8px rgba(0,0,0,.06);font-size:13px;color:#8a9297;padding:14px 20px}
.map{position:absolute;left:649px;top:3314px;width:420px;height:378px;border-radius:22px;background:linear-gradient(135deg,#e4ece3,#d7e3ea 55%,#e9e4d8)}
.map-card{position:absolute;left:10px;top:10px;width:290px;height:86px;background:var(--white);border-radius:4px;box-shadow:0 1px 4px rgba(0,0,0,.2);padding:10px 14px;font-size:12px;color:var(--ink)}
.map-card small{display:block;font-size:10px;color:#666;margin-top:4px}
.map-card a{display:block;font-size:10px;color:#1a73e8;margin-top:14px;text-decoration:none}

/* footer */
.site-footer{position:absolute;left:0;top:3846px;width:1200px;height:406px;background:var(--dark);color:var(--white)}
.foot-brand-dot{position:absolute;left:120px;top:124px;width:100px;height:100px;border-radius:50%;background:var(--green)}
.foot-brand{position:absolute;left:80px;top:236px;width:180px;text-align:center;font-size:20px;font-weight:500}
.social{position:absolute;top:290px;width:36px;height:36px;border:1.5px solid var(--white);border-radius:50%}
.foot-h{position:absolute;top:126px;font-size:23px;font-weight:500}
.foot-h::after{content:"";position:absolute;left:0;top:44px;width:190px;height:1px;background:rgba(255,255,255,.55)}
.qlinks{position:absolute;left:366px;top:189px;list-style:none}
.qlinks li{font-size:13.5px;height:26.5px;display:flex;align-items:center;gap:10px}
.qlinks li::before{content:"";width:8px;height:8px;border:1.5px solid var(--green);transform:rotate(45deg)}
.fc-item{position:absolute;left:594px;display:flex;gap:16px;align-items:center;font-size:13px;line-height:16px}
.fc-ico{width:34px;height:34px;border:1.5px solid var(--white);border-radius:8px;transform:rotate(45deg);display:flex;align-items:center;justify-content:center;flex:none}
.fc-ico svg{transform:rotate(-45deg)}
.news-text{position:absolute;left:895px;top:188px;width:225px;font-size:13px;line-height:18px}
.news-input{position:absolute;left:888px;top:267px;width:208px;height:34px;border:1.5px solid var(--white);border-radius:20px;font-size:11.5px;padding:9px 16px}
.news-go{position:absolute;right:4px;top:4px;width:24px;height:24px;border:1.5px solid var(--white);border-radius:50%;display:flex;align-items:center;justify-content:center}
.copyright{position:absolute;left:0;top:4252px;width:1200px;height:71px;background:var(--green);text-align:center;font-size:12.5px;line-height:71px;color:var(--ink)}
</style>
</head>
<body>

<!-- background decoration -->
<div class="blob" style="left:-330px;top:1400px;width:680px;height:680px;border-radius:160px"></div>
<div class="blob" style="left:820px;top:2120px;width:700px;height:700px;border-radius:170px"></div>
<div class="blob" style="left:-360px;top:3120px;width:560px;height:560px;border-radius:140px"></div>

<header class="site-header">
  <div class="brand"><span class="brand-dot"></span><span class="brand-name">Tollbrook Advisory</span></div>
  <nav class="main-nav">
    <a class="active" href="#" style="left:0">HOME</a>
    <a href="#" style="left:79px">WHO WE ARE</a>
    <a href="#" style="left:208px">OUR SERVICES</a>
    <a href="#" style="left:347px">TEAM</a>
    <a href="#" style="left:418px">CONTACT US</a>
  </nav>
</header>

<section class="hero" role="img" aria-label="City skyline with glass towers and a high-rise residential building against a blue sky">
  <div class="hero-towers"></div>
  <div class="hero-mid"></div>
  <div class="hero-building"></div>
  <div class="hero-shape"></div>
  <div class="hero-copy">
    <h1 class="hero-title">Building Success</h1>
    <p class="hero-sub">in Southern California</p>
    <p class="hero-kicker">Expertise at Every Step:</p>
    <p class="hero-kicker2">From Planning to Execution</p>
  </div>
  <a class="pill" style="left:262px;top:478px;width:194px;height:58px">LEARN MORE<span class="knob"></span></a>
</section>

<!-- about -->
<section class="about">
  <h2 class="h2" style="left:97px;top:1000px">About Us</h2>
  <div class="kicker" style="left:97px;top:1058px">Who We Are <span class="rule"></span></div>
  <p class="about-text">Welcome to Tollbrook Advisory, your trusted partner in navigating the complexities of the real estate and small business markets. Founded by industry veterans Daniel Ferrante and Owen Takeda, we specialize in providing comprehensive services tailored to the unique needs of our clients. Whether you're a franchisee, a new restaurant owner, or a commercial real estate investor, our expertise in due diligence</p>
  <a class="pill" style="left:100px;top:1352px;width:196px;height:59px">READ MORE<span class="knob"></span></a>
  <div class="about-halo"></div>
  <div class="about-photo" role="img" aria-label="Dense city block of residential towers with a rooftop water tank"></div>
</section>

<!-- services -->
<section class="services">
  <h2 class="h2" style="left:0;width:1200px;text-align:center;top:1636px">Our Services</h2>
  <div class="kicker" style="left:476px;top:1697px"><span class="rule short"></span>What We Do<span class="rule short"></span></div>

  <article class="svc-card" style="left:70px;top:1817px;width:326px;height:413px">
    <div class="svc-img" role="img" aria-label="Business handshake in front of an office window" style="background:linear-gradient(135deg,#dcdfe2,#9ea7ae 60%,#6b747b)"></div>
    <div class="svc-icon" style="top:166px"><svg width="34" height="34" viewBox="0 0 34 34" fill="none" stroke="#25323b" stroke-width="1.6"><path d="M5 13h24l-2-6H7z"/><path d="M7 13v15h20V13"/><rect x="13" y="19" width="8" height="9"/></svg></div>
    <h3 class="svc-title" style="top:268px">Franchise Development</h3>
    <p class="svc-desc" style="top:306px">Comprehensive franchise setup from evaluation to launch for scalable business growth.</p>
  </article>

  <article class="svc-card featured" style="left:436px;top:1794px;width:322px;height:448px">
    <div class="svc-img" role="img" aria-label="Two colleagues reviewing documents at a desk" style="background:linear-gradient(135deg,#e9e6e1,#b9b1a8 55%,#7e8c97)"></div>
    <div class="svc-icon" style="top:166px"><svg width="34" height="34" viewBox="0 0 34 34" fill="none" stroke="#25323b" stroke-width="1.6"><circle cx="11" cy="11" r="5"/><rect x="14" y="14" width="13" height="16"/><path d="M17 20h7M17 24h7"/></svg></div>
    <h3 class="svc-title" style="top:268px">Due Diligence</h3>
    <p class="svc-desc" style="top:306px">Tollbrook offers comprehensive evaluations tailored to your business needs.</p>
    <svg class="abs" style="left:144px;top:390px" width="34" height="24" viewBox="0 0 34 24" fill="none" stroke="#25323b" stroke-width="1.6"><path d="M8 12h18M20 6l6 6-6 6"/><path d="M12 4 4 12l8 8"/></svg>
  </article>

  <article class="svc-card" style="left:792px;top:1817px;width:326px;height:413px">
    <div class="svc-img" role="img" aria-label="Construction team in hard hats studying plans on a table" style="background:linear-gradient(135deg,#c9d2da,#8ea4b7 55%,#5c6f80)"></div>
    <div class="svc-icon" style="top:166px"><svg width="34" height="34" viewBox="0 0 34 34" fill="none" stroke="#25323b" stroke-width="1.6"><circle cx="11" cy="11" r="5"/><rect x="14" y="14" width="13" height="16"/><path d="M17 20h7M17 24h7"/></svg></div>
    <h3 class="svc-title" style="top:268px">Construction Management</h3>
    <p class="svc-desc" style="top:306px">Our Building &amp; Construction Management Services oversee every aspect of your construction</p>
  </article>
</section>

<!-- team -->
<section class="team">
  <h2 class="h2" style="left:0;width:1200px;text-align:center;top:2364px">Our Team</h2>
  <div class="kicker" style="left:452px;top:2421px"><span class="rule short"></span>Tollbrook Advisory<span class="rule short"></span></div>

  <article class="team-card" style="left:237px;top:2539px">
    <div class="team-photo" role="img" aria-label="Portrait of Daniel Ferrante outdoors above a hillside view" style="background:linear-gradient(180deg,#a9c4df,#c5c9c4 55%,#8a8f7e)"></div>
    <h3 class="team-name">Daniel Ferrante</h3>
    <p class="team-role">Principal</p>
    <span class="team-rule"></span>
    <span class="team-ico" style="left:222px"><svg width="16" height="16" viewBox="0 0 16 16" fill="#fff"><path d="M4 1l3 3-2 2c1 2 3 4 5 5l2-2 3 3-2 3C7 15 1 9 1 3z"/></svg></span>
    <span class="team-ico" style="left:266px"><svg width="16" height="16" viewBox="0 0 16 16" fill="none" stroke="#fff" stroke-width="1.5"><rect x="2" y="4" width="12" height="9"/><path d="M2 4l6 5 6-5"/></svg></span>
    <p class="team-bio">Daniel Ferrante brings almost 20 years of rich experience as a real estate...</p>
  </article>

  <article class="team-card" style="left:643px;top:2539px">
    <div class="team-photo" role="img" aria-label="Portrait of Owen Takeda against a dark brown backdrop" style="background:linear-gradient(180deg,#5a4a3c,#3a2f27)"></div>
    <h3 class="team-name">Owen Takeda</h3>
    <p class="team-role">Principal</p>
    <span class="team-rule"></span>
    <span class="team-ico" style="left:222px"><svg width="16" height="16" viewBox="0 0 16 16" fill="#fff"><path d="M4 1l3 3-2 2c1 2 3 4 5 5l2-2 3 3-2 3C7 15 1 9 1 3z"/></svg></span>
    <span class="team-ico" style="left:266px"><svg width="16" height="16" viewBox="0 0 16 16" fill="none" stroke="#fff" stroke-width="1.5"><rect x="2" y="4" width="12" height="9"/><path d="M2 4l6 5 6-5"/></svg></span>
    <p class="team-bio">Owen Takeda is a seasoned real estate expert with extensive experience in...</p>
  </article>
</section>

<!-- contact -->
<section class="contact">
  <h2 class="h2" style="left:118px;top:3184px">Contact Us</h2>
  <div class="kicker" style="left:120px;top:3243px">Get In Touch <span class="rule" style="width:142px"></span></div>
  <p class="contact-lead">Encouraging visitors to get in touch with us for consultations or further information.</p>
  <div class="field" style="left:118px;top:3442px;width:223px;height:47px">Name</div>
  <div class="field" style="left:361px;top:3442px;width:223px;height:47px">Phone</div>
  <div class="field" style="left:118px;top:3507px;width:466px;height:46px">Email Address</div>
  <div class="field" style="left:118px;top:3574px;width:466px;height:98px">Message</div>
  <a class="pill light" style="left:121px;top:3717px;width:171px;height:57px;padding-left:28px">SUBMIT<span class="knob"></span></a>

  <div class="map" role="img" aria-label="Street map showing the office location at 210 Harbor Point Dr Suite 4">
    <div class="map-card">210 Harbor Point Dr Suite 4<small>210 Harbor Point Dr, Suite 4</small><a>View larger map</a></div>
    <svg class="abs" style="left:325px;top:160px" width="26" height="34" viewBox="0 0 26 34"><path d="M13 33C5 20 1 16 1 12a12 12 0 0 1 24 0c0 4-4 8-12 21z" fill="#e0443a"/><circle cx="13" cy="12" r="4" fill="#8a1c16"/></svg>
  </div>
</section>

<!-- footer -->
<footer class="site-footer">
  <span class="foot-brand-dot"></span>
  <p class="foot-brand">Tollbrook Advisory</p>
  <span class="social" style="left:83px"></span>
  <span class="social" style="left:130px"></span>
  <span class="social" style="left:175px"></span>
  <span class="social" style="left:222px"></span>

  <h4 class="foot-h" style="left:366px">Quik Links</h4>
  <ul class="qlinks">
    <li>Home</li><li>Who We Are</li><li>Our Services</li><li>Team</li><li>Contact Us</li>
  </ul>

  <h4 class="foot-h" style="left:594px">Contact</h4>
  <div class="fc-item" style="top:190px"><span class="fc-ico"><svg width="14" height="14" viewBox="0 0 16 16" fill="#fff"><path d="M4 1l3 3-2 2c1 2 3 4 5 5l2-2 3 3-2 3C7 15 1 9 1 3z"/></svg></span><span>CALL US<br>555 014 2280</span></div>
  <div class="fc-item" style="top:239px"><span class="fc-ico"><svg width="14" height="14" viewBox="0 0 16 16" fill="none" stroke="#fff" stroke-width="1.5"><rect x="2" y="4" width="12" height="9"/><path d="M2 4l6 5 6-5"/></svg></span><span>EMAIL US<br>hello@tollbrookadvisory.example</span></div>
  <div class="fc-item" style="top:289px"><span class="fc-ico"><svg width="14" height="14" viewBox="0 0 16 16" fill="none" stroke="#fff" stroke-width="1.5"><path d="M8 15C4 10 3 8 3 6a5 5 0 0 1 10 0c0 2-1 4-5 9z"/><circle cx="8" cy="6" r="1.8"/></svg></span><span>Address line here dummy<br>Address line here</span></div>

  <h4 class="foot-h" style="left:889px">Our Newsletter</h4>
  <p class="news-text">Get all the latest information on Special Discounts, Products and Offers.</p>
  <div class="news-input">Enter Email Address<span class="news-go"><svg width="12" height="12" viewBox="0 0 12 12" fill="none" stroke="#fff" stroke-width="1.4"><path d="M2 6h8M7 3l3 3-3 3"/></svg></span></div>
</footer>
<div class="copyright">Copyright © 2024 All Rights Reserved By Company name</div>

</body>
</html>
```